Quillford Air Business Card Design

Design new, 2 sides, business cards for a residential and light commercial heating, air conditioning contractor.

Target Market(s)

Homeowners, small businesses

Industry/Entity Type

Business

Contact Information for Business Card

Dominic Westerhall
Phone - 862-415-2736
Email
Address - PO box 518
Brightwater NJ 07912
Website - www.QuillfordAirLLC.example

Requirements
Must have
• logo, company colors, standard size with no die cut, so I can use nova stamp

```html
<!DOCTYPE html>
<html lang="en">
<head>
<meta charset="utf-8">
<title>Quillford Air Business Card</title>
<link rel="stylesheet" href="https://fonts.googleapis.com/css2?family=Barlow+Semi+Condensed:wght@400;500;600&family=Roboto:wght@400&display=swap">
<style>
  :root {
    --backdrop: #e6e6e6;
    --card: #0b0b0c;
    --maroon: #7e2331;
    --cream: #f1d59c;
    --gold: #f2c21b;
    --strip: #e0b21a;
    --white: #ffffff;
  }
  * { box-sizing: border-box; margin: 0; padding: 0; }
  html, body { width: 1200px; height: 576px; overflow: hidden; }
  body { background: var(--backdrop); position: relative; font-family: "Barlow Semi Condensed", Arial, sans-serif; }

  .card {
    position: absolute;
    top: 138px;
    height: 294px;
    background: var(--card);
    overflow: hidden;
  }
  .card--front { left: 81px; width: 485px; }
  .card--back { left: 602px; width: 481px; height: 292px; }

  .brand-name {
    position: absolute;
    font-family: "Barlow Semi Condensed", Arial, sans-serif;
    font-weight: 600;
    color: var(--cream);
    line-height: 1;
    white-space: nowrap;
    display: flex;
    align-items: center;
    justify-content: center;
    gap: 10px;
  }
  .brand-name__mark {
    width: 12px; height: 12px;
    background: var(--cream);
    border-radius: 50%;
    flex: none;
  }
  .card--front .brand-name { left: 0; right: 0; top: 112px; font-size: 40px; }
  .card--back .brand-name { left: 30px; width: 200px; top: 127px; font-size: 30px; }

  .service-band {
    position: absolute;
    left: 0; right: 0; top: 247px;
    height: 27px;
    background: var(--maroon);
    color: var(--cream);
    font-family: "Roboto", Arial, sans-serif;
    font-size: 12.5px;
    display: flex;
    align-items: center;
    justify-content: center;
  }

  .person { position: absolute; left: 254px; top: 81px; }
  .person__name { color: var(--gold); font-weight: 600; font-size: 19px; line-height: 1.1; }
  .person__title { color: var(--white); font-size: 11.5px; margin-top: 3px; }

  .contact-list { position: absolute; left: 254px; top: 136px; list-style: none; }
  .contact-list li {
    display: flex; align-items: center; gap: 11px;
    color: var(--white); font-size: 12.5px; height: 16.6px;
  }
  .contact-list svg { width: 12px; height: 12px; fill: var(--gold); flex: none; }

  .accent-strip { position: absolute; left: 0; right: 0; bottom: 0; height: 6px; background: var(--strip); }
</style>
</head>
<body>
  <section class="card card--front">
    <div class="brand-name"><span class="brand-name__mark"></span>Quillford Air</div>
    <div class="service-band">Residential &amp; Light Commercial Heating &nbsp;• Air Conditioning Contractor</div>
  </section>

  <section class="card card--back">
    <div class="brand-name"><span class="brand-name__mark"></span>Quillford Air</div>
    <div class="person">
      <p class="person__name">Dominic Westerhall</p>
      <p class="person__title">Managing Director</p>
    </div>
    <ul class="contact-list">
      <li><svg viewBox="0 0 24 24"><path d="M2 8c3-4 17-4 20 0l-3 3-3-2V7H8v2l-3 2zM5 13h14l2 8H3z"/></svg>862-415-2736</li>
      <li><svg viewBox="0 0 24 24"><path d="M2 5h20v14H2z M3 6l9 7 9-7" stroke="#0b0b0c" stroke-width="1.5"/></svg>info@QuillfordAirLLC.example</li>
      <li><svg viewBox="0 0 24 24"><circle cx="12" cy="12" r="10"/><path d="M2 12h20M12 2c-5 5-5 15 0 20M12 2c5 5 5 15 0 20" stroke="#0b0b0c" stroke-width="1.5" fill="none"/></svg>www.QuillfordAirLLC.example</li>
      <li><svg viewBox="0 0 24 24"><path d="M12 1a8 8 0 0 0-8 8c0 6 8 14 8 14s8-8 8-14a8 8 0 0 0-8-8zm0 11a3 3 0 1 1 0-6 3 3 0 0 1 0 6z"/></svg>PO box 518 Brightwater NJ 07912</li>
    </ul>
    <div class="accent-strip"></div>
  </section>
</body>
</html>
```